iPhone iOS 7 App For Managing Tasks/Photos for Internal Company Use

We need an app design that displays company objectives and task, and provides the interface for employees to complete a task by uploading a photo and adding comments.

Please see attached mock up sketches as a rough guideline

Final delivery of files must contain PSD, and all layers/objects sliced both is PSD and PNG files

Target Market(s)

This is a tool for internal employee use

Industry/Entity Type

It Company

Requirements
Must have
• Must include logo, and match the colour scheme
Use iPhone iOS 7 Style

```html
<!DOCTYPE html>
<html lang="en">
<head>
<meta charset="utf-8">
<title>Sign In</title>
<link href="https://fonts.googleapis.com/css2?family=Open+Sans:wght@400;600&display=swap" rel="stylesheet">
<style>
  :root {
    --screen-bg: #a7b9c5;
    --header-bg: #ffffff;
    --brand: #4f7580;
    --card-bg: #f4f5f5;
    --field-bg: #4a6870;
    --field-text: #ffffff;
    --action: #e84b2f;
    --title-text: #3c3f41;
    --status-text: #111111;
  }
  * { box-sizing: border-box; margin: 0; padding: 0; }
  html, body { width: 675px; height: 1200px; overflow: hidden; }
  body {
    background: var(--screen-bg);
    font-family: "Open Sans", sans-serif;
    position: relative;
  }
  .status-bar {
    position: absolute; top: 0; left: 0; width: 675px; height: 51px;
    display: flex; align-items: center; justify-content: space-between;
    padding: 0 14px; color: var(--status-text); font-size: 21px;
  }
  .status-left, .status-right { display: flex; align-items: center; gap: 8px; }
  .status-time { position: absolute; left: 0; right: 0; text-align: center; font-weight: 600; pointer-events: none; }
  .app-header {
    position: absolute; top: 51px; left: 0; width: 675px; height: 84px;
    background: var(--header-bg);
    box-shadow: 0 2px 4px rgba(0,0,0,0.18);
    display: flex; align-items: center; justify-content: center; gap: 16px;
  }
  .brand-dot { width: 40px; height: 40px; border-radius: 50%; background: var(--brand); }
  .brand-name { color: var(--brand); font-size: 33px; font-weight: 600; letter-spacing: 0.5px; }
  .signin-card {
    position: absolute; left: 84px; top: 407px; width: 475px; height: 425px;
    background: var(--card-bg); border-radius: 9px; overflow: hidden;
  }
  .signin-title {
    height: 92px; display: flex; align-items: center; justify-content: center;
    font-size: 30px; color: var(--title-text); padding-top: 8px;
  }
  .field {
    height: 96px; background: var(--field-bg); color: var(--field-text);
    display: flex; align-items: center; padding-left: 36px; gap: 28px; font-size: 28px;
  }
  .field + .field { margin-top: 14px; }
  .field svg { width: 34px; height: 34px; }
  .login-button {
    position: absolute; left: 0; bottom: 0; width: 100%; height: 97px;
    background: var(--action); color: #fff; font-size: 28px;
    display: flex; align-items: center; justify-content: center;
  }
</style>
</head>
<body>
  <div class="status-bar">
    <div class="status-left">
      <svg width="74" height="14" viewBox="0 0 74 14" aria-hidden="true">
        <circle cx="7" cy="7" r="6" fill="#111"/><circle cx="22" cy="7" r="6" fill="#111"/><circle cx="37" cy="7" r="6" fill="#111"/>
        <circle cx="52" cy="7" r="5.3" fill="none" stroke="#111" stroke-width="1.4"/><circle cx="67" cy="7" r="5.3" fill="none" stroke="#111" stroke-width="1.4"/>
      </svg>
      <span>NOVA</span>
      <svg width="24" height="18" viewBox="0 0 24 18" aria-hidden="true">
        <path d="M12 17 L2 6 A14 14 0 0 1 22 6 Z" fill="#111"/>
      </svg>
    </div>
    <div class="status-time">4:21 PM</div>
    <div class="status-right">
      <svg width="14" height="22" viewBox="0 0 14 22" aria-hidden="true">
        <path d="M2 6 L12 16 L7 21 L7 1 L12 6 L2 16" fill="none" stroke="#555" stroke-width="1.6"/>
      </svg>
      <span>100%</span>
      <svg width="52" height="22" viewBox="0 0 52 22" aria-hidden="true">
        <rect x="1" y="1" width="46" height="20" rx="3" fill="none" stroke="#111" stroke-width="1.6"/>
        <rect x="4" y="4" width="40" height="14" rx="1" fill="#111"/>
        <rect x="48" y="7" width="3" height="8" fill="#111"/>
      </svg>
    </div>
  </div>

  <header class="app-header">
    <span class="brand-dot"></span>
    <span class="brand-name">KESTREL</span>
  </header>

  <main class="signin-card">
    <h1 class="signin-title">SIGN IN TO CONTINUE</h1>
    <div class="field field-email">
      <svg viewBox="0 0 34 34" aria-hidden="true">
        <circle cx="17" cy="11" r="6.5" fill="none" stroke="#fff" stroke-width="2.6"/>
        <path d="M8 18 H26 Q29 24 30 30 H4 Q5 24 8 18 Z" fill="none" stroke="#fff" stroke-width="2.6" stroke-linejoin="round"/>
      </svg>
      <span>Email</span>
    </div>
    <div class="field field-password">
      <svg viewBox="0 0 34 34" aria-hidden="true">
        <path d="M12 22 A9 9 0 1 1 22 22 V25 H12 Z" fill="none" stroke="#fff" stroke-width="2.6" stroke-linejoin="round"/>
        <line x1="13" y1="29" x2="21" y2="29" stroke="#fff" stroke-width="2.6"/>
      </svg>
      <span>Password</span>
    </div>
    <div class="login-button">LOG IN</div>
  </main>
</body>
</html>
```